Oriel Photography Business Card

I need a business card designed for a photography business based in Perth, Western Australia called Oriel Photography.

We specialise in wedding, event photography and portrait photography.

The business card must borrow the style of the attached logo.

The hex codes for the colours in the logo are:
#ED1D85 - Pink
#89C23E - Green
#37282F - Black

The name on the card will be:
Name: Tobrian
Phone: 0417395268
Website: www.orielphotography.example.com.au
social: orielphotography

I am open and happy to accept creative concepts.

I’d like some space at the back for writing notes and appointment details.

```html
<!DOCTYPE html>
<html lang="en">
<head>
<meta charset="utf-8">
<title>Oriel Photography – Business Card</title>
<link rel="stylesheet" href="https://fonts.googleapis.com/css2?family=Raleway:wght@400&family=Open+Sans:wght@400;600;700&display=swap">
<style>
  :root {
    --pink: #ED1D85;
    --green: #89C23E;
    --ink: #37282F;
    --ink-dark: #2a2029;
    --grey-stripe: #7d7580;
    --paper: #ffffff;
    --backdrop: #ecebea;
  }
  * { box-sizing: border-box; margin: 0; padding: 0; }
  html, body { width: 1200px; height: 1000px; overflow: hidden; }
  body { background: var(--backdrop); position: relative; font-family: "Open Sans", sans-serif; }

  .card {
    position: absolute;
    width: 600px; height: 350px;
    background: var(--paper);
    box-shadow: 0 8px 24px rgba(0,0,0,0.18);
    overflow: hidden;
  }
  .card-shapes { position: absolute; inset: 0; width: 100%; height: 100%; }

  .brand-dot { width: 44px; height: 44px; border-radius: 50%; background: var(--pink); flex: none; }
  .brand-name {
    font-family: "Raleway", sans-serif; font-weight: 400;
    color: var(--ink); text-transform: uppercase;
    white-space: nowrap;
  }

  /* Front */
  .card-front { left: 90px; top: 110px; }
  .card-front .brand {
    position: absolute; left: 0; top: 50px; width: 600px;
    display: flex; flex-direction: column; align-items: center; gap: 22px;
  }
  .card-front .brand-name { font-size: 14px; letter-spacing: 9px; }

  /* Back */
  .card-back { left: 510px; top: 530px; }
  .card-back .brand {
    position: absolute; left: 20px; top: 28px; width: 300px;
    display: flex; flex-direction: column; align-items: center; gap: 12px;
  }
  .card-back .brand-name { font-size: 13px; letter-spacing: 7px; }
  .tagline {
    position: absolute; left: 36px; top: 110px;
    font-size: 10.5px; font-weight: 600; color: var(--ink);
    white-space: nowrap;
  }
  .person-name {
    position: absolute; left: 70px; top: 188px;
    font-size: 19px; font-weight: 700; color: var(--pink);
  }
  .contact-list {
    position: absolute; left: 352px; top: 170px;
    list-style: none; display: flex; flex-direction: column; gap: 6px;
  }
  .contact-item {
    display: flex; align-items: center; gap: 6px;
    color: var(--green); font-size: 11px; white-space: nowrap;
  }
  .contact-mark {
    width: 14px; height: 14px; background: var(--pink);
    color: var(--paper); font-size: 9px; font-weight: 700;
    display: flex; align-items: center; justify-content: center; flex: none;
  }
</style>
</head>
<body>

  <section class="card card-front" aria-label="Business card front">
    <svg class="card-shapes" viewBox="0 0 600 350" aria-hidden="true">
      <path d="M0,350 L0,275 C120,258 250,262 360,232 C460,204 540,182 600,152 L600,350 Z" fill="var(--ink-dark)"/>
      <path d="M330,222 C440,190 530,162 600,134" fill="none" stroke="var(--ink-dark)" stroke-width="5"/>
    </svg>
    <div class="brand">
      <span class="brand-dot"></span>
      <span class="brand-name">Oriel Photography</span>
    </div>
  </section>

  <section class="card card-back" aria-label="Business card back">
    <svg class="card-shapes" viewBox="0 0 600 350" aria-hidden="true">
      <path d="M200,0 L270,0 C335,50 352,120 346,185 C332,100 290,40 200,0 Z" fill="var(--grey-stripe)"/>
      <path d="M600,0 L250,0 C325,60 348,150 332,230 C320,290 292,330 270,350 L600,350 Z" fill="var(--ink-dark)"/>
    </svg>
    <div class="brand">
      <span class="brand-dot"></span>
      <span class="brand-name">Oriel Photography</span>
    </div>
    <p class="tagline">Wedding-Event Photography-Portrait Photography</p>
    <p class="person-name">Tobrian</p>
    <ul class="contact-list">
      <li class="contact-item"><span class="contact-mark">P</span>0417395268</li>
      <li class="contact-item"><span class="contact-mark">W</span>www.orielphotography.example.com.au</li>
      <li class="contact-item"><span class="contact-mark"></span>social/orielphotography</li>
    </ul>
  </section>

</body>
</html>
```